Naturopath Practitioner Card Design

I am a naturopath needing a design for a business card mainly to show that I am a naturopath and have some contact details to give to prospective clients. I am open minded about the design and what is on the second side of the card whether it just be some artwork or space for details, appointment times etc. Naturopathy is the practice of natural medicine that uses a holistic approach and incorporates herbal and nutritional medicine.

Industry/Entity Type

Business

Contact Information for Business Card

Tom Rudd NaturopathBHSc (Naturopathy) Member WHPG 0487 925 316 tom.rudd@mailexample.com www.tomruddnaturopathy.example.au

Requirements
Nice to have
• Would prefer some kind of original pattern/art work/logo rather than an image, not fussed if its very simple/basic
• I am open to any colour but think I would prefer a more earthy sandy clay etc type style than the greens that are commonly associated with naturopathy.
Should not have
• Don't really want to have generic stock images on it

```html
<!DOCTYPE html>
<html lang="en">
<head>
<meta charset="utf-8">
<title>Tom Rudd Naturopath – Business Card</title>
<link rel="stylesheet" href="https://fonts.googleapis.com/css2?family=Open+Sans:wght@400;600;700&display=swap">
<style>
  :root {
    --stage: #2f3134;
    --card: #ffffff;
    --green: #2aa20f;
    --green-dark: #1f8a0a;
    --ink: #1a1a1a;
    --box: #8a8a8a;
  }
  * { box-sizing: border-box; margin: 0; padding: 0; }
  html, body {
    width: 1200px; height: 864px; overflow: hidden;
    background: var(--stage);
    font-family: "Open Sans", Arial, sans-serif;
  }
  .card {
    position: absolute;
    left: 290px;
    width: 620px; height: 350px;
    background: var(--card);
    box-shadow: 0 6px 18px rgba(0,0,0,.35);
  }
  .card--appointment { top: 50px; }
  .card--contact { top: 460px; }

  /* appointment side */
  .appt-band {
    position: absolute; left: 0; right: 0; top: 22px; height: 54px;
    background: var(--green);
    color: #fff; font-weight: 700; font-size: 22px;
    display: flex; align-items: center; justify-content: center;
  }
  .appt-field {
    position: absolute; display: flex; align-items: flex-end;
    font-weight: 700; font-size: 15px; color: var(--ink);
  }
  .appt-field .fill {
    border-bottom: 2px dotted var(--ink);
    margin-left: 4px; height: 12px;
  }
  .field-name { left: 110px; top: 104px; }
  .field-name .fill { width: 335px; }
  .field-date { left: 90px; top: 154px; }
  .field-date .fill { width: 120px; margin-right: 14px; }
  .field-date .fill.time { width: 110px; margin-right: 6px; }
  .field-date .ampm { font-weight: 400; font-size: 16px; }
  .days {
    position: absolute; left: 60px; right: 60px; top: 202px;
    display: flex; justify-content: space-between; list-style: none;
  }
  .day {
    display: flex; align-items: center; gap: 6px;
    color: var(--green); font-size: 13px; font-weight: 600;
  }
  .day::before {
    content: ""; width: 20px; height: 16px;
    border: 2px solid var(--box);
  }
  .appt-note {
    position: absolute; left: 0; right: 0; top: 262px;
    text-align: center; color: var(--green);
    font-weight: 700; font-size: 16px;
  }

  /* contact side */
  .identity {
    position: absolute; left: 0; right: 0; top: 92px; text-align: center;
    color: var(--ink);
  }
  .identity .name {
    color: var(--green); font-weight: 700; font-size: 32px;
    letter-spacing: 1px; line-height: 1;
  }
  .identity .role { font-size: 19px; font-weight: 600; line-height: 1.2; }
  .identity .credentials { font-size: 13px; }
  .contacts {
    position: absolute; left: 0; right: 0; top: 232px;
    list-style: none; text-align: center; color: var(--ink); font-size: 16px;
  }
  .contacts li {
    display: flex; align-items: center; justify-content: center; gap: 8px;
    line-height: 26px;
  }
  .contacts svg { fill: var(--green); }
</style>
</head>
<body>
  <section class="card card--appointment" aria-label="Appointment side">
    <div class="appt-band">Your Next Appointment on</div>
    <div class="appt-field field-name">Name :<span class="fill"></span></div>
    <div class="appt-field field-date">Date :<span class="fill"></span>Time :<span class="fill time"></span><span class="ampm">AM / PM</span></div>
    <ul class="days">
      <li class="day">MON</li>
      <li class="day">TUE</li>
      <li class="day">WED</li>
      <li class="day">THU</li>
      <li class="day">FRI</li>
      <li class="day">SAT</li>
    </ul>
    <p class="appt-note">If unable to keep appointment, kindly give 24hrs notice.</p>
  </section>

  <section class="card card--contact" aria-label="Contact side">
    <div class="identity">
      <h1 class="name">TOM RUDD</h1>
      <p class="role">Naturopath</p>
      <p class="credentials">BHSc (Naturopathy) Member WHPG</p>
    </div>
    <ul class="contacts">
      <li>
        <svg width="15" height="15" viewBox="0 0 24 24" aria-hidden="true"><path d="M6.6 10.8a15.1 15.1 0 0 0 6.6 6.6l2.2-2.2c.3-.3.7-.4 1-.2 1.1.4 2.3.6 3.6.6.6 0 1 .4 1 1V20c0 .6-.4 1-1 1A17 17 0 0 1 3 4c0-.6.4-1 1-1h3.5c.6 0 1 .4 1 1 0 1.3.2 2.5.6 3.6.1.3 0 .7-.2 1z"/></svg>
        0487 925 316
      </li>
      <li>
        <svg width="20" height="14" viewBox="0 0 20 14" aria-hidden="true"><rect width="20" height="14" rx="1"/><path d="M1 1l9 7 9-7" fill="none" stroke="#fff" stroke-width="1.5"/></svg>
        tom.rudd@mailexample.com
      </li>
    </ul>
  </section>
</body>
</html>
```